Blue Harbor Mortgages Social Media Campaign

I need social media campaign banners. Facebook and Instagram.
I would like them to incorporate local photos, my photo and my logo. I have some sample files of previous campaigns and I have a color scheme associated with my brand. My business operates in St. John's Newfoundland.

Target Market(s)

Home Buyers, Home Owners

Industry/Entity Type

Mortgage Brokering

Logo Text

Blue Harbor Mortgages

Logo styles of interest
Lettermark Logo
Font styles to use
Other font styles liked:
• Times New Roman, I'm open to suggestion

Colors
0054AA
0677BA
7BADD7
CADEEF
E8F1F8
EE7325
F08F49
F5BC92
FAE3D3
FDF4ED

Requirements
Must have
• My name, photo, contact info, slogan
Nice to have
• We can discuss slogans to use, I can provide some suggestions.

```html
<!DOCTYPE html>
<html lang="en">
<head>
<meta charset="utf-8">
<title>Blue Harbor Mortgages – Social Campaign</title>
<link rel="stylesheet" href="https://fonts.googleapis.com/css2?family=Poppins:wght@300;400;500;600;700;800&display=swap">
<style>
  :root{
    --navy:#0b1852;
    --orange:#fb4a0c;
    --ink:#1c1c1c;
    --white:#ffffff;
    --stage:#d4d4d4;
    --rule:#9aa3ad;
  }
  *{box-sizing:border-box;margin:0;padding:0}
  html,body{width:966px;height:1200px;overflow:hidden;background:var(--stage)}
  body{position:relative;font-family:'Poppins',sans-serif;color:var(--ink)}

  .post{position:absolute;overflow:hidden;background:var(--white);box-shadow:0 10px 30px rgba(0,0,0,.25)}
  .post--square{left:135px;top:96px;width:700px;height:700px}
  .post--wide{left:199px;top:840px;width:571px;height:285px}

  .photo{position:absolute;inset:0}
  .post--square .photo{
    background:
      linear-gradient(100deg,rgba(255,255,255,1) 0%,rgba(255,255,255,.85) 40%,rgba(255,255,255,0) 75%) top/100% 62% no-repeat,
      linear-gradient(180deg,#ffffff 0%,#eef1f4 22%,#d2dae2 42%,#b9c4cd 52%,#7e9260 60%,#5c7a3e 70%,#6f7a5a 80%,#8b6a5e 88%,#5d6f78 100%);
  }
  .post--wide .photo{
    background:
      linear-gradient(90deg,rgba(255,255,255,0) 0%,rgba(255,255,255,0) 35%,rgba(255,255,255,.9) 60%,#fff 100%) top/100% 60% no-repeat,
      linear-gradient(180deg,#ffffff 0%,#e9edf1 25%,#c4ced6 45%,#6e8852 58%,#5a773d 70%,#7c7a5a 82%,#6a7f86 100%);
  }

  .base{position:absolute;left:0;top:0;width:100%;height:100%}

  .headline{position:absolute;font-weight:700;line-height:1;white-space:nowrap;text-transform:uppercase}
  .headline .accent{color:var(--orange)}
  .headline .navy{color:var(--navy)}

  /* square post */
  .sq-line1{left:41px;top:33px;font-size:46px;letter-spacing:-2px}
  .sq-line2{left:40px;top:72px;font-size:60px;letter-spacing:-1.5px;color:var(--orange)}
  .sq-line3{left:39px;top:123px;font-size:57px;letter-spacing:-2.2px;color:var(--navy)}
  .sq-line4{left:41px;top:176px;font-size:43px;letter-spacing:-1.5px}
  .sq-rule{position:absolute;left:41px;top:232px;width:509px;height:1px;background:var(--rule)}
  .sq-bar{position:absolute;left:66px;top:228px;width:92px;height:8px;border-radius:4px;background:var(--orange)}
  .sq-lede{position:absolute;left:41px;top:246px;font-size:18px;font-weight:300;line-height:23px;color:var(--ink)}
  .sq-lede strong{font-weight:700}

  .brand-name{position:absolute;font-weight:700;color:var(--orange);white-space:nowrap;letter-spacing:-.2px;text-transform:uppercase}
  .brand-mark{position:absolute;background:var(--white)}
  .sq-brand{left:65px;top:545px;font-size:14.5px}
  .sq-mark{left:117px;top:496px;width:38px;height:38px}

  .agent{position:absolute;font-weight:700;white-space:nowrap;color:var(--white);line-height:1;text-transform:uppercase}
  .agent .surname{color:var(--orange);margin-left:.35em}
  .sq-agent{left:51px;top:589px;font-size:31px;letter-spacing:-.3px}

  .cta{position:absolute;display:flex;align-items:center;justify-content:center;background:var(--orange);color:var(--white);font-weight:700;border-radius:999px;white-space:nowrap;text-transform:uppercase}
  .sq-cta{left:49px;top:627px;width:129px;height:26px;font-size:12.5px}

  .contact{position:absolute;display:flex;align-items:center;white-space:nowrap;color:var(--white);font-weight:700;line-height:1}
  .contact svg{flex:none}
  .sq-phone{left:186px;top:624px;font-size:27px;gap:4px;letter-spacing:.3px}
  .sq-mail{left:439px;top:607px;font-size:14.5px;gap:6px;font-weight:600}
  .sq-web{left:439px;top:635px;font-size:14.5px;gap:6px;font-weight:600}

  /* wide banner */
  .wd-line1{right:19px;top:19px;font-size:22px;font-weight:400;letter-spacing:-.3px;color:var(--ink)}
  .wd-line2{right:18px;top:37px;font-size:37px;letter-spacing:-1.2px;color:var(--orange)}
  .wd-line3{right:19px;top:73px;font-size:23px;letter-spacing:-.6px}
  .wd-rule{position:absolute;left:226px;top:104px;width:326px;height:1px;background:#c6ccd2}
  .wd-bar{position:absolute;left:499px;top:102px;width:44px;height:3px;border-radius:2px;background:var(--orange)}
  .wd-lede{position:absolute;right:19px;top:114px;font-size:11.3px;font-weight:300;line-height:14px;text-align:right;color:var(--ink)}
  .wd-lede strong{font-weight:700}
  .wd-brand{left:32px;top:60px;font-size:11px}
  .wd-mark{left:72px;top:22px;width:26px;height:26px;background:var(--navy)}
  .wd-cta{left:38px;top:214px;width:100px;height:21px;font-size:10px}
  .wd-agent{left:26px;top:246px;font-size:14.5px;letter-spacing:-.1px}
  .wd-phone{left:180px;top:248px;font-size:11.5px;gap:2px}
  .wd-mail{left:284px;top:250px;font-size:8.3px;gap:3px;font-weight:600}
  .wd-web{left:424px;top:250px;font-size:8.3px;gap:3px;font-weight:600}
</style>
</head>
<body>

<!-- Square feed post -->
<section class="post post--square">
  <div class="photo" role="img" aria-label="Photo of colourful houses on a green, rocky hillside above a harbour under a cloudy sky"></div>

  <h1 class="headline sq-line1">Building your</h1>
  <div class="headline sq-line2">Dream home</div>
  <div class="headline sq-line3">One mortgage</div>
  <div class="headline sq-line4">At a time</div>
  <div class="sq-rule"></div>
  <div class="sq-bar"></div>
  <p class="sq-lede">Let Us Help You Unlock Your<br><strong>DREAM HOME TODAY</strong> With Low<br>Rates &amp; Great Deals!</p>

  <svg class="base" viewBox="0 0 700 700" aria-hidden="true">
    <polygon points="0,518 145,432 292,526 700,526 700,700 0,700" fill="var(--orange)"/>
    <polygon points="0,533 145,447 289,538 700,538 700,700 0,700" fill="var(--white)"/>
    <polygon points="0,538 144,452 287,543 700,543 700,700 0,700" fill="var(--navy)"/>
  </svg>

  <div class="brand-mark sq-mark"></div>
  <div class="brand-name sq-brand">Blue Harbor Mortgages</div>

  <div class="agent sq-agent">Marlee<span class="surname">Dawson</span></div>
  <div class="cta sq-cta">Get started ››</div>

  <div class="contact sq-phone">
    <svg width="20" height="22" viewBox="0 0 24 24"><path d="M6.6 10.8a15.1 15.1 0 0 0 6.6 6.6l2.2-2.2a1 1 0 0 1 1-.25 11.4 11.4 0 0 0 3.6.57 1 1 0 0 1 1 1V20a1 1 0 0 1-1 1A17 17 0 0 1 3 4a1 1 0 0 1 1-1h3.5a1 1 0 0 1 1 1c0 1.25.2 2.45.57 3.57a1 1 0 0 1-.25 1z" fill="var(--orange)"/></svg>
    709-555-0142
  </div>
  <div class="contact sq-mail">
    <svg width="15" height="11" viewBox="0 0 15 11"><rect x=".5" y=".5" width="14" height="10" fill="var(--orange)"/><polyline points=".8,.8 7.5,6 14.2,.8" fill="none" stroke="var(--navy)" stroke-width="1.2"/></svg>
    info@bayviewlending.com
  </div>
  <div class="contact sq-web">
    <svg width="15" height="15" viewBox="0 0 16 16" fill="none" stroke="var(--orange)" stroke-width="1.4"><circle cx="8" cy="8" r="7"/><ellipse cx="8" cy="8" rx="3" ry="7"/><line x1="1" y1="8" x2="15" y2="8"/></svg>
    www.bayviewlending.com
  </div>
</section>

<!-- Wide cover banner -->
<section class="post post--wide">
  <div class="photo" role="img" aria-label="Photo of colourful houses on a green, rocky hillside above a harbour under a cloudy sky"></div>

  <div class="brand-mark wd-mark"></div>
  <div class="brand-name wd-brand">Blue Harbor Mortgages</div>

  <h2 class="headline wd-line1">Building your</h2>
  <div class="headline wd-line2">Dream home</div>
  <div class="headline wd-line3"><span class="navy">One mortgage</span> at a time</div>
  <div class="wd-rule"></div>
  <div class="wd-bar"></div>
  <p class="wd-lede">Let Us Help You Unlock Your<br><strong>DREAM HOME TODAY</strong> With Low<br>Rates &amp; Great Deals!</p>

  <svg class="base" viewBox="0 0 571 285" aria-hidden="true">
    <polygon points="0,197 88,144 194,210 571,210 571,285 0,285" fill="var(--orange)"/>
    <polygon points="0,206 88,154 191,218 571,218 571,285 0,285" fill="var(--white)"/>
    <polygon points="0,210 88,158 189,222 571,222 571,285 0,285" fill="var(--navy)"/>
  </svg>

  <div class="cta wd-cta">Get started ››</div>
  <div class="agent wd-agent">Marlee<span class="surname">Dawson</span></div>
  <div class="contact wd-phone">
    <svg width="10" height="10" viewBox="0 0 24 24"><path d="M6.6 10.8a15.1 15.1 0 0 0 6.6 6.6l2.2-2.2a1 1 0 0 1 1-.25 11.4 11.4 0 0 0 3.6.57 1 1 0 0 1 1 1V20a1 1 0 0 1-1 1A17 17 0 0 1 3 4a1 1 0 0 1 1-1h3.5a1 1 0 0 1 1 1c0 1.25.2 2.45.57 3.57a1 1 0 0 1-.25 1z" fill="var(--orange)"/></svg>
    709-555-0142
  </div>
  <div class="contact wd-mail">
    <svg width="8" height="6" viewBox="0 0 15 11"><rect x=".5" y=".5" width="14" height="10" fill="var(--orange)"/><polyline points=".8,.8 7.5,6 14.2,.8" fill="none" stroke="var(--navy)" stroke-width="1.4"/></svg>
    info@bayviewlending.com
  </div>
  <div class="contact wd-web">
    <svg width="9" height="9" viewBox="0 0 16 16" fill="none" stroke="var(--orange)" stroke-width="1.6"><circle cx="8" cy="8" r="7"/><ellipse cx="8" cy="8" rx="3" ry="7"/><line x1="1" y1="8" x2="15" y2="8"/></svg>
    www.bayviewlending.com
  </div>
</section>

</body>
</html>
```